Title: Iron Ledger Sub: She never leaves the harbor - Book cover

I need a complete book cover, front, spine, and back.

Religions Book

This book is more about the Title so it should be strong and serious.

Like the color Deep Red and black, blue. Deep purple
Avoid greens, orange, yellows.

Maybe a picture of a strong hand on the Bible. OR someone yelling.

If any pictures are used they must be 100% royalty free with proof or a buyout of image.

I have attached a couple of designs that the client likes. Just as a reference. The exception they DIDN'T like the pictures in the book cover.

Please ask any questions to clarify.

Please see the file I just uploaded called 'Book Cover samples.png" The clients likes the Title: Salt and Ember" the best. Please create a design something closer to this. The like how the title jumps off the page with a 2D look.

Again the Title must standout, and any use of images must be a secondary to the design.

I am happy with we the designs that have been submitted so far.

I hope this helps you get closer.

Thank you

First of all I want to thank you for all of your designs. At the beginning the client thought he would like a picture that represented the title. But after looking at all of the designs. He has now decided NOT to have any pictures.

Here is what he wants

1. BOLD Font (San Serif only) no fancy versions for the Title "IRON LEDGER" in uppercase. The title font should have some dimension to it to appear 2D or 3D looks. Shiny look. It needs to looks like it jumping off the page.

2. The subtitle right below the title in San Serif font)

3. Background solid color either black, dark red, or dark blue. The background can be slightly textured or gradation fill, etc.

4. The cover must have a strong and bold statement.

Thank you again.

Please use this photo on the back cover.

Thank you

Requirements
Should not have
• A picture that over powers the Title.

```html
<!DOCTYPE html>
<html lang="en">
<head>
<meta charset="utf-8">
<title>Iron Ledger – Book Cover</title>
<link rel="stylesheet" href="https://fonts.googleapis.com/css2?family=Oswald:wght@500;600;700&family=Open+Sans:wght@700&family=Roboto+Condensed:wght@400&display=swap">
<style>
  :root {
    --canvas: #e6e6e6;
    --blue-deep: #1f2f7a;
    --blue-mid: #34489e;
    --purple: #5a2f86;
    --red-deep: #9c1d2a;
    --red-dark: #3a0a10;
    --black-red: #1c0508;
    --title-red-light: #ff5a66;
    --title-red: #d81f33;
    --title-purple-light: #b45ee0;
    --title-purple: #7a2fb0;
    --white: #ffffff;
    --rule: rgba(255,255,255,0.85);
    --box: rgba(10,2,4,0.55);
  }
  * { box-sizing: border-box; margin: 0; padding: 0; }
  html, body { width: 1200px; height: 800px; overflow: hidden; background: var(--canvas); }

  .spread { position: absolute; left: 160px; top: 80px; width: 880px; height: 640px; display: flex; box-shadow: 0 18px 40px rgba(0,0,0,0.25); }

  /* ---------- Back cover ---------- */
  .back-cover {
    width: 420px; height: 640px; position: relative;
    background: linear-gradient(180deg, var(--blue-deep) 0%, #2a2263 35%, #4a1230 65%, var(--red-dark) 85%, var(--black-red) 100%);
    color: var(--white); text-align: center; padding: 26px 30px 0;
  }
  .back-author { font-family: "Open Sans", sans-serif; font-weight: 700; font-size: 15px; text-align: right; padding-right: 10px; letter-spacing: 0.5px; }
  .back-title {
    font-family: "Oswald", sans-serif; font-weight: 600; font-size: 52px; line-height: 1.05; margin-top: 2px;
    background: linear-gradient(180deg, var(--title-red-light), var(--title-red) 60%, var(--purple));
    -webkit-background-clip: text; background-clip: text; color: transparent;
    filter: drop-shadow(1px 2px 0 rgba(0,0,0,0.6));
  }
  .back-subtitle { font-family: "Oswald", sans-serif; font-weight: 600; font-size: 21px; letter-spacing: 0.3px; margin: 8px 0; }
  .back-blurb {
    font-family: "Roboto Condensed", sans-serif; font-size: 11.5px; line-height: 1.32; text-align: justify; text-align-last: center;
    margin-top: 20px; color: #f2f2f2;
  }
  .back-boxes { position: absolute; left: 30px; right: 30px; bottom: 24px; display: flex; justify-content: space-between; }
  .placeholder-box {
    width: 118px; height: 78px; background: var(--box);
    font-family: "Open Sans", sans-serif; font-weight: 700; font-size: 10px; color: var(--white);
    display: flex; align-items: center; justify-content: center;
  }

  .divider { display: flex; align-items: center; gap: 8px; }
  .divider .rule { flex: 1; height: 1px; background: var(--rule); }
  .divider .ornament { width: 34px; height: 8px; border-radius: 4px; background: var(--rule); }

  /* ---------- Spine ---------- */
  .spine {
    width: 40px; height: 640px;
    background: linear-gradient(180deg, var(--blue-deep) 0%, var(--purple) 50%, var(--red-deep) 80%, var(--red-dark) 100%);
    display: flex; align-items: center; justify-content: flex-start; flex-direction: column; padding-top: 22px;
    box-shadow: inset 3px 0 6px rgba(0,0,0,0.35), inset -3px 0 6px rgba(0,0,0,0.35);
  }
  .spine-text { writing-mode: vertical-rl; white-space: nowrap; }
  .spine-subtitle { font-family: "Oswald", sans-serif; font-weight: 500; font-size: 11px; color: var(--white); }
  .spine-title {
    font-family: "Oswald", sans-serif; font-weight: 700; font-size: 25px; margin-top: 18px;
    color: var(--title-red); text-shadow: 1px 1px 0 rgba(0,0,0,0.5);
  }
  .spine-author { font-family: "Open Sans", sans-serif; font-weight: 700; font-size: 10px; color: var(--white); margin-top: auto; margin-bottom: 22px; }

  /* ---------- Front cover ---------- */
  .front-cover {
    width: 420px; height: 640px; position: relative; overflow: hidden; text-align: center; color: var(--white);
    background: linear-gradient(180deg, var(--blue-mid) 0%, #3c4aa8 22%, #4d2f85 50%, #7a1f4a 72%, var(--red-deep) 88%, #6a1018 100%);
  }
  .front-artwork {
    position: absolute; left: 0; top: 0; width: 420px; height: 330px;
    background: radial-gradient(ellipse at 48% 48%, rgba(255,255,255,0.85) 0%, rgba(225,232,255,0.55) 22%, rgba(150,170,230,0.25) 50%, rgba(60,74,168,0) 75%);
  }
  .front-title {
    position: relative; font-family: "Oswald", sans-serif; font-weight: 600; line-height: 1; letter-spacing: 1px;
    filter: drop-shadow(2px 3px 0 rgba(40,0,20,0.55)) drop-shadow(0 0 8px rgba(255,255,255,0.25));
  }
  .front-title .line-one {
    display: block; font-size: 118px; padding-top: 48px;
    background: linear-gradient(180deg, var(--title-red-light), var(--title-red) 70%);
    -webkit-background-clip: text; background-clip: text; color: transparent;
  }
  .front-title .line-two {
    display: block; font-size: 112px; margin-top: 4px;
    background: linear-gradient(180deg, var(--title-purple-light), var(--title-purple) 70%, #5a2390);
    -webkit-background-clip: text; background-clip: text; color: transparent;
  }
  .front-divider { position: relative; margin: 16px 18px 0; }
  .front-subtitle {
    position: relative; font-family: "Oswald", sans-serif; font-weight: 600; font-size: 44px; line-height: 1.1;
    margin: 10px 0 12px; text-shadow: 1px 2px 2px rgba(0,0,0,0.4);
  }
  .front-author {
    position: absolute; left: 0; right: 0; bottom: 40px;
    font-family: "Open Sans", sans-serif; font-weight: 700; font-size: 24px; letter-spacing: 0.5px;
  }
</style>
</head>
<body>
  <div class="spread">
    <section class="back-cover">
      <p class="back-author">CALEB NORWOOD'S</p>
      <h2 class="back-title">IRON LEDGER</h2>
      <div class="divider"><span class="rule"></span><span class="ornament"></span><span class="rule"></span></div>
      <p class="back-subtitle">SHE NEVER LEAVES THE HARBOR</p>
      <div class="divider"><span class="rule"></span><span class="ornament"></span><span class="rule"></span></div>
      <p class="back-blurb">Lorem ipsum dolor sit amet, consectetur adipisicing elit, sed do eiusmod tempor incididunt ut labore et dolore magna aliqua. Ut enim ad minim veniam, quis nostrud exercitation. Lorem ipsum dolor sit amet, consectetur adipisicing elit, sed do eiusmod tempor incididunt ut labore et dolore magna aliqua. Ut enim ad minim veniam, quis nostrud exercitation. Lorem ipsum dolor sit amet, consectetur adipisicing elit, sed do eiusmod tempor incididunt ut labore et dolore magna aliqua. Ut enim ad minim veniam, quis nostrud exercitation. Lorem ipsum dolor sit amet, consectetur adipisicing elit, sed do eiusmod tempor incididunt ut labore et dolore magna aliqua. Ut enim ad minim veniam, quis nostrud exercitation. Lorem ipsum dolor sit amet, consectetur adipisicing elit, sed do eiusmod tempor incididunt ut labore et dolore magna aliqua. Ut enim ad minim veniam, quis nostrud exercitation. Lorem ipsum dolor sit amet, consectetur adipisicing elit, sed do eiusmod tempor incididunt ut labore et dolore magna aliqua. Ut enim ad minim veniam, quis nostrud exercitation.</p>
      <div class="back-boxes">
        <div class="placeholder-box">LOGO</div>
        <div class="placeholder-box">ISBN</div>
      </div>
    </section>

    <section class="spine">
      <span class="spine-text spine-subtitle">SHE NEVER LEAVES THE HARBOR</span>
      <span class="spine-text spine-title">IRON LEDGER</span>
      <span class="spine-text spine-author">CALEB NORWOOD</span>
    </section>

    <section class="front-cover">
      <div class="front-artwork" role="img" aria-label="White doves flying through sunlit clouds"></div>
      <h1 class="front-title"><span class="line-one">IRON</span><span class="line-two">LEDGER</span></h1>
      <div class="divider front-divider"><span class="rule"></span><span class="ornament"></span><span class="rule"></span></div>
      <p class="front-subtitle">SHE NEVER LEAVES<br>THE HARBOR</p>
      <div class="divider front-divider" style="margin-top:0"><span class="rule"></span><span class="ornament"></span><span class="rule"></span></div>
      <p class="front-author">CALEB NORWOOD</p>
    </section>
  </div>
</body>
</html>
```